Electrician Business Card/ company logo/small business

New Business Cards and logo needed that will catch peoples eye and say we went that extra step. Attached is a design possibly to be incorporated, if u have your own great, lets see it!... This will be a small local business. thank you for all you do!
Halvern Electric
Ned Fosky Owner
Journeyman Electrician
phone 1.555.208.3471
email: KQLHalvernElectric@quellmail.net
call for free estimate!
Updates

Accepted and approved for cards

Target Market(s)

support small local business

Industry/Entity Type

Electrical,

Contact Information for Business Card

name, title,company/ logo, phone, email, free estimate

Other font styles liked:
• easy to read

Colors

Designer to choose colors to be used in the design.

Requirements
Must have
• eye catching everything! logo and halvern electric listed on business card/logo, incorp logo in the background of card
Nice to have
• lightening bolts in eyes or around the triangle? vertical, modern, any design that would be unique and stand out
Should not have
• pinks, reds, yellows,brown

```html
<!DOCTYPE html>
<html lang="en">
<head>
<meta charset="utf-8">
<title>Halvern Electric – Business Card</title>
<link rel="stylesheet" href="https://fonts.googleapis.com/css2?family=Orbitron:wght@700&family=Open+Sans:wght@400;600&family=Roboto+Condensed:wght@500&display=swap">
<style>
  :root {
    --backdrop: #6f93c4;
    --card-dark: #1f1f1f;
    --card-top: #2a2b2d;
    --facet: #303133;
    --facet-soft: #262728;
    --accent-orange: #ee8a24;
    --accent-red: #e32227;
    --icon-orange: #e0763a;
    --text-white: #f4f4f4;
    --rule-grey: #3a3a3a;
  }
  html, body {
    margin: 0;
    width: 1200px;
    height: 1200px;
    overflow: hidden;
    background: var(--backdrop);
  }
  .business-card {
    position: absolute;
    left: 300px;
    top: 100px;
    width: 600px;
    height: 1000px;
    background: var(--card-dark);
    overflow: hidden;
  }
  .card-background {
    position: absolute;
    inset: 0;
  }
  .brand-lockup {
    position: absolute;
    left: 61px;
    top: 140px;
    display: flex;
    align-items: center;
    gap: 22px;
  }
  .brand-square {
    width: 62px;
    height: 62px;
    background: var(--accent-orange);
  }
  .brand-name {
    font-family: "Orbitron", sans-serif;
    font-weight: 700;
    font-size: 44px;
    line-height: 1.1;
    color: var(--text-white);
    letter-spacing: 1px;
    margin: 0;
  }
  .person-name {
    position: absolute;
    left: 61px;
    top: 478px;
    margin: 0;
    font-family: "Orbitron", sans-serif;
    font-weight: 700;
    font-size: 46px;
    letter-spacing: 2px;
    color: var(--accent-orange);
  }
  .person-role {
    position: absolute;
    left: 61px;
    top: 537px;
    margin: 0;
    font-family: "Roboto Condensed", sans-serif;
    font-weight: 500;
    font-size: 33px;
    color: var(--text-white);
  }
  .title-rule {
    position: absolute;
    left: 61px;
    top: 593px;
    width: 407px;
    height: 3px;
    background: var(--rule-grey);
  }
  .title-rule::before {
    content: "";
    position: absolute;
    left: 0;
    top: 0;
    width: 169px;
    height: 3px;
    background: var(--accent-orange);
  }
  .person-trade {
    position: absolute;
    left: 63px;
    top: 610px;
    margin: 0;
    font-family: "Open Sans", sans-serif;
    font-weight: 400;
    font-size: 29px;
    letter-spacing: 1px;
    color: var(--text-white);
  }
  .contact-row {
    position: absolute;
    left: 72px;
    display: flex;
    align-items: center;
    gap: 19px;
  }
  .contact-phone { top: 755px; }
  .contact-email { top: 834px; }
  .contact-icon {
    width: 55px;
    height: 51px;
    background: var(--icon-orange);
    display: flex;
    align-items: center;
    justify-content: center;
  }
  .contact-phone .contact-text {
    font-family: "Open Sans", sans-serif;
    font-weight: 600;
    font-size: 40px;
    color: var(--text-white);
  }
  .contact-email .contact-text {
    font-family: "Open Sans", sans-serif;
    font-weight: 600;
    font-size: 23px;
    color: var(--text-white);
  }
</style>
</head>
<body>
  <main class="business-card">
    <svg class="card-background" width="600" height="1000" viewBox="0 0 600 1000" aria-hidden="true">
      <rect class="top-panel" x="0" y="0" width="600" height="420" fill="var(--card-top)"/>
      <polygon class="facet" points="0,0 260,0 120,150 0,90" fill="var(--facet)" opacity="0.6"/>
      <polygon class="facet" points="260,0 600,0 600,120 380,210" fill="var(--facet)" opacity="0.5"/>
      <polygon class="facet" points="0,170 200,120 168,306 0,368" fill="var(--facet-soft)" opacity="0.8"/>
      <polygon class="lower-panel" points="0,368 168,306 600,500 600,1000 0,1000" fill="var(--card-dark)"/>
      <polygon class="facet" points="0,650 170,560 300,1000 0,1000" fill="var(--facet-soft)" opacity="0.5"/>
      <polygon class="facet" points="600,560 430,720 600,900" fill="var(--facet-soft)" opacity="0.5"/>
      <polygon class="accent-red" points="310,368 495,285 600,355 600,368" fill="var(--accent-red)"/>
      <polygon class="accent-orange" points="495,285 600,239 600,355" fill="var(--accent-orange)"/>
    </svg>

    <div class="brand-lockup">
      <div class="brand-square"></div>
      <p class="brand-name">HALVERN<br>ELECTRIC</p>
    </div>

    <h1 class="person-name">NED FOSKY</h1>
    <p class="person-role">OWNER</p>
    <div class="title-rule"></div>
    <p class="person-trade">JOURNEYMAN ELECTRICIAN</p>

    <div class="contact-row contact-phone">
      <div class="contact-icon">
        <svg width="30" height="26" viewBox="0 0 30 26" aria-hidden="true">
          <path d="M2 8 Q15 0 28 8 L26 12 L21 10 L20 7 Q15 5 10 7 L9 10 L4 12 Z" fill="#fff"/>
          <path d="M8 12 H22 L26 23 H4 Z" fill="#fff"/>
          <circle cx="15" cy="17" r="3" fill="var(--icon-orange)"/>
        </svg>
      </div>
      <span class="contact-text">1.555.208.3471</span>
    </div>

    <div class="contact-row contact-email">
      <div class="contact-icon">
        <svg width="32" height="22" viewBox="0 0 32 22" aria-hidden="true">
          <rect x="1" y="1" width="30" height="20" fill="none" stroke="#fff" stroke-width="2"/>
          <polyline points="1,1 16,13 31,1" fill="none" stroke="#fff" stroke-width="2"/>
          <line x1="1" y1="21" x2="12" y2="10" stroke="#fff" stroke-width="2"/>
          <line x1="31" y1="21" x2="20" y2="10" stroke="#fff" stroke-width="2"/>
        </svg>
      </div>
      <span class="contact-text">kqlhalvernelectric@quellmail.net</span>
    </div>
  </main>
</body>
</html>
```